4th Generation Family Business Needs a New Card Design!

We are a family owned 4th Generation company. We are based in the Sydney, Australia area and we are desperately in need of a more modern and classy card. We are monumental masons who design, supply & erect lasting memorials throughout cemeteries in Sydney. Our customers are normally in a period of grieving. I have attached logo files that will need to be implemented on the card. Company was established 1935. Australian Owned and Operated. Card needs to be designed to PIXO.com specification.

Target Market(s)

Our target market is based upon people that a grieving for family members that have passed away. We also deal with alot of companies that own and operate cemeteries.

Industry/Entity Type

Business

Contact Information for Business Card

Simon Harcourt, Operations Manager, 0417293086, simon@harcourtmemorials.com.au
Lewis Harcourt, Director, 0491630572, lewis@harcourtmemorials.com.au
Phone # 02 9561 3048
Website: www.harcourtmemorials.com.au
Address: Suite 17, 8 Palfrey Lane, West Carlow, Sydney NSW 2156

Font styles to use
Serif
Decorative
Script

Requirements
Must have
• Would like to see the logo nicely implemented with a modern design. Embossed lettering would be a nice additive.

```html
<!DOCTYPE html>
<html lang="en">
<head>
<meta charset="utf-8">
<title>Harcourt Memorials – Business Card</title>
<link rel="stylesheet" href="https://fonts.googleapis.com/css2?family=Cinzel:wght@500;600&family=Open+Sans:ital,wght@0,400;1,400&display=swap">
<style>
  :root {
    --backdrop: #e6e6e6;
    --paper: #f4f4f5;
    --ink: #1d1d1d;
    --gold: #c9a527;
    --gold-text: #c3a12d;
    --grey-text: #555759;
    --divider: #b8b8b8;
  }
  * { box-sizing: border-box; margin: 0; padding: 0; }
  html, body { width: 1105px; height: 1200px; overflow: hidden; }
  body {
    background: var(--backdrop);
    font-family: "Open Sans", Arial, sans-serif;
    position: relative;
  }
  .card {
    position: absolute;
    left: 180px;
    width: 746px;
    height: 425px;
    overflow: hidden;
  }
  .card-front { top: 120px; background: var(--paper); }
  .card-back { top: 650px; background: var(--gold); }

  .brand-name {
    font-family: "Cinzel", Georgia, serif;
    font-weight: 600;
    color: var(--ink);
    text-align: center;
    line-height: 1.05;
    letter-spacing: 1px;
  }
  .card-front .brand-name {
    position: absolute;
    left: 30px; width: 310px;
    top: 128px;
    font-size: 44px;
  }
  .brand-name .sub { display: block; font-size: 0.62em; letter-spacing: 3px; }

  .divider {
    position: absolute;
    left: 356px; top: 88px;
    width: 1px; height: 250px;
    background: var(--divider);
  }
  .contact { position: absolute; left: 384px; top: 86px; }
  .person-name {
    font-family: "Cinzel", Georgia, serif;
    font-weight: 600;
    font-size: 30px;
    color: var(--ink);
    letter-spacing: 1px;
    line-height: 1.1;
  }
  .person-title {
    font-family: "Cinzel", Georgia, serif;
    font-weight: 500;
    font-size: 19px;
    color: var(--gold-text);
    letter-spacing: 1px;
    margin-top: 2px;
  }
  .address {
    margin-top: 16px;
    font-size: 18.5px;
    line-height: 27px;
    color: var(--grey-text);
  }
  .details { list-style: none; margin-top: 12px; }
  .details li {
    display: flex; align-items: center;
    font-size: 18.5px; line-height: 29px;
    color: var(--grey-text);
  }
  .details svg { width: 16px; height: 16px; margin-right: 12px; flex: none; fill: var(--ink); }

  .card-band { position: absolute; left: 0; bottom: 0; width: 746px; height: 29px; }

  .card-back .brand-name {
    position: absolute;
    left: 0; width: 746px;
    top: 150px;
    font-size: 60px;
  }
  .card-back .web {
    position: absolute;
    left: 0; width: 746px;
    top: 348px;
    text-align: center;
    font-style: italic;
    font-size: 21px;
    letter-spacing: 1px;
    color: var(--ink);
  }
</style>
</head>
<body>
  <section class="card card-front">
    <div class="brand-name">Harcourt<span class="sub">Memorials</span></div>
    <div class="divider"></div>
    <div class="contact">
      <h1 class="person-name">Simon Harcourt</h1>
      <p class="person-title">Operations Manager</p>
      <p class="address">Suite 17, 8 Palfrey Lane<br>West Carlow, Sydney NSW 2156</p>
      <ul class="details">
        <li><svg viewBox="0 0 16 16" aria-hidden="true"><path d="M3.2 1 5.6 3.6 4.3 5.6c.8 2.2 2.9 4.4 5.5 5.9l2-1.3 2.6 2.4-1.6 2.4C7.6 14.4 1.8 8.6 1 3z"/></svg>02 9561 3048</li>
        <li><svg viewBox="0 0 16 16" aria-hidden="true"><path d="M4 0h8a1 1 0 0 1 1 1v14a1 1 0 0 1-1 1H4a1 1 0 0 1-1-1V1a1 1 0 0 1 1-1zm1 2v10h6V2zm3 11a1 1 0 1 0 0 2 1 1 0 0 0 0-2z"/></svg>0417293086</li>
        <li><svg viewBox="0 0 16 16" aria-hidden="true"><path d="M0 3h16v1.2L8 9 0 4.2zm0 2.6 8 4.8 8-4.8V13H0z"/></svg>simon@harcourtmemorials.com.au</li>
        <li><svg viewBox="0 0 16 16" aria-hidden="true"><circle cx="8" cy="8" r="7.5"/><path d="M4 5.5 7 6l-.5 3 2 1.5-1 3.5-2-4L3 8zM9.5 3l3 1 .5 4-2-1z" fill="#f4f4f5"/></svg>www.harcourtmemorials.com.au</li>
      </ul>
    </div>
    <svg class="card-band" viewBox="0 0 746 29" aria-hidden="true">
      <polygon points="0,0 490,0 480,29 0,29" fill="var(--ink)"/>
      <polygon points="497,0 746,0 746,29 487,29" fill="var(--gold)"/>
    </svg>
  </section>

  <section class="card card-back">
    <div class="brand-name">Harcourt<span class="sub">Memorials</span></div>
    <p class="web">www.harcourtmemorials.com.au</p>
  </section>
</body>
</html>
```